Photography Business, Business Card

Looking for a unique cutting edge card that takes advantage of the latest printing technologies. Please review this site for all the options they office: https://glowprintly.com. If you can think it they can do it. And if you have an idea and do not know if they can do it, I will check into it.

Target Market(s)

People and places I took images of and future clients.

Industry/Entity Type

Photography

Contact Information for Business Card

Name, cell & email. Derek Holloway, dholloway@kpnvisuals.com, 312-748-2961

Colors

Designer to choose only greyscale colors for use in the design.

Requirements
Must have
• 100% cutting edge. Is so great, those I hand it to always show it to someone else. A piece of art.
Nice to have
• Blacks, silvers, greys, some red. Maybe other colors?

```html
<!DOCTYPE html>
<html lang="en">
<head>
<meta charset="utf-8">
<title>Derek Holloway – Business Card</title>
<link rel="stylesheet" href="https://fonts.googleapis.com/css2?family=Mrs+Saint+Delafield&family=Open+Sans:wght@400;600;700&display=swap">
<style>
  :root {
    --page: #1c1c1c;
    --card: #121212;
    --frame: #8e8e8e;
    --text: #8c8c8c;
    --script: #9a9a9a;
    --aperture-light: #555555;
    --aperture-dark: #393939;
    --rec: #ff1a1a;
    --battery: #1fa51f;
    --brand: #e3222b;
  }
  * { margin: 0; padding: 0; box-sizing: border-box; }
  html, body { width: 1200px; height: 1200px; overflow: hidden; background: var(--page); }
  .canvas { position: relative; width: 1200px; height: 1200px; }
  .card {
    position: absolute; left: 250px; width: 700px; height: 400px;
    background: var(--card); border-radius: 18px; overflow: hidden;
    font-family: "Open Sans", sans-serif;
  }
  .card--front { top: 165px; }
  .card--back { top: 634px; }
  .viewfinder { position: absolute; inset: 0; }
  .rec { position: absolute; left: 46px; top: 44px; display: flex; align-items: center; gap: 3px;
    color: var(--frame); font-size: 12px; font-weight: 700; }
  .rec__dot { width: 12px; height: 12px; border-radius: 50%; background: var(--rec); }
  .battery { position: absolute; left: 610px; top: 42px; }
  .name-first { position: absolute; left: 58px; top: 58px; color: var(--script);
    font-family: "Mrs Saint Delafield", cursive; font-size: 112px; line-height: 1; white-space: nowrap; }
  .name-last { position: absolute; left: 173px; top: 144px; color: var(--script);
    font-size: 17px; letter-spacing: 4px; white-space: nowrap; font-weight: 400; }
  .contacts { position: absolute; left: 64px; top: 252px; list-style: none; color: var(--text);
    font-size: 16px; letter-spacing: 0.8px; }
  .contacts li { display: flex; align-items: center; gap: 9px; height: 26px; white-space: nowrap; }
  .contacts svg { width: 14px; height: 14px; flex: none; }
  .aperture {
    position: absolute; width: 320px; height: 320px; border-radius: 50%;
    background: radial-gradient(circle at 50% 40%, var(--aperture-light), var(--aperture-dark));
  }
  .card--front .aperture { left: 323px; top: 40px; }
  .card--back .aperture { left: 55px; top: 39px; }
  .brand { position: absolute; left: 427px; top: 159px; width: 212px; text-align: center;
    color: var(--brand); font-size: 58px; font-weight: 600; letter-spacing: 6px; line-height: 80px; }
</style>
</head>
<body>
<main class="canvas">
  <section class="card card--front">
    <svg class="viewfinder" width="700" height="400" viewBox="0 0 700 400" fill="none" stroke="#8e8e8e" stroke-width="2">
      <polyline points="27,161 27,27 160,27"/>
      <polyline points="27,239 27,372 160,372"/>
      <polyline points="540,27 673,27 673,161"/>
      <polyline points="540,372 673,372 673,239"/>
    </svg>
    <div class="rec"><span class="rec__dot"></span>REC</div>
    <svg class="battery" width="44" height="20" viewBox="0 0 44 20">
      <rect x="4" y="1" width="39" height="18" fill="none" stroke="#8e8e8e" stroke-width="1.5"/>
      <rect x="0" y="6" width="4" height="8" fill="none" stroke="#8e8e8e" stroke-width="1.5"/>
      <rect x="7" y="4" width="6" height="12" fill="var(--battery)"/>
      <rect x="15" y="4" width="6" height="12" fill="var(--battery)"/>
      <rect x="23" y="4" width="6" height="12" fill="var(--battery)"/>
      <rect x="31" y="4" width="6" height="12" fill="var(--battery)"/>
    </svg>
    <div class="name-first">Derek</div>
    <div class="name-last">HOLLOWAY</div>
    <ul class="contacts">
      <li><svg viewBox="0 0 14 14" fill="none" stroke="#8c8c8c" stroke-width="1.5"><rect x="3.5" y="1" width="7" height="12" rx="1.2"/><line x1="6" y1="11" x2="8" y2="11"/></svg>312-748-2961</li>
      <li><svg viewBox="0 0 14 14" fill="#8c8c8c"><path d="M1 3h12v8H1z"/><path d="M1 3l6 5 6-5" fill="none" stroke="#121212" stroke-width="1.2"/></svg>dholloway@kpnvisuals.com</li>
      <li><svg viewBox="0 0 14 14" fill="none" stroke="#8c8c8c" stroke-width="1.4"><circle cx="7" cy="7" r="6"/><path d="M1 7h12M7 1c-3 3-3 9 0 12M7 1c3 3 3 9 0 12"/></svg>www.zyvimages.com</li>
    </ul>
    <div class="aperture" role="img" aria-label="Large grey camera aperture graphic with a small lens at its centre"></div>
  </section>

  <section class="card card--back">
    <div class="aperture" role="img" aria-label="Large grey camera aperture graphic with a small lens at its centre"></div>
    <div class="brand">ZYV</div>
  </section>
</main>
</body>
</html>
```